Event Website Design

We need a new website design for an events driven website. The domain for this site is http://brackmoorhalls.co.uk. The site is up and running but needs a new fresh, modern look.
I've attached a Balamiq Mockup for the layout of the home page. Also attached is a png of the logo.
Key colours for the site are 0f7e6a, 35bde, d57835 & 373737.
Font to use is Proxima Nova
Width of the site should be 1200px
The design should be contemporary with minimal clutter.
Websites to references are…
http://vorpin.london/
http://www.darvushall.co.uk/
These are just guidelines, please feel free to use you own creative judgment.
The selected design file needs to be supplied as an editable PSD.
Reason: I've submitted 5 designs to the client, who will select the one they want. I will then choose that design. So please be patient as I'm waiting for a decision from my client.
Industry/Entity Type
Events
Number of Pages Required
1 page
Look and feel
Each slider illustrates characteristics of the customer's brand and the style your logo design should communicate.

```html
<!DOCTYPE html>
<html lang="en">
<head>
<meta charset="utf-8">
<title>Brackmoor Halls</title>
<link href="https://fonts.googleapis.com/css2?family=Figtree:wght@400;600;700&display=swap" rel="stylesheet">
<style>
:root{
  --teal:#0f7e6a;
  --blue:#035bde;
  --orange:#d57835;
  --charcoal:#373737;
  --nav:#3d3d3d;
  --paper:#efefef;
  --white:#ffffff;
  --ink:#444444;
  --muted:#666666;
}
*{margin:0;padding:0;box-sizing:border-box}
html,body{width:1200px;height:2667px;overflow:hidden}
body{position:relative;font-family:"Figtree",Arial,sans-serif;background:var(--white);color:var(--ink)}
.abs{position:absolute}
a{color:inherit;text-decoration:none}

/* header */
.site-header{left:0;top:0;width:1200px;height:121px;background:var(--charcoal)}
.brand{left:73px;top:34px;color:var(--white);font-weight:700;font-size:25px;line-height:26px;letter-spacing:1px}
.brand-divider{left:240px;top:24px;width:1px;height:74px;background:#555}
.tagline{left:263px;top:49px;color:var(--white);font-size:15px}
.util-links{right:75px;top:16px;color:#ddd;font-size:11.5px}
.util-links span{margin:0 5px;color:#888}
.box-office{left:715px;top:65px;color:#eee;font-size:18px}
.box-office b{color:var(--orange);font-weight:600}
.search{left:972px;top:60px;width:153px;height:32px;border-radius:16px;background:var(--white);color:#999;font-size:12px;padding:8px 0 0 34px}
.search svg{position:absolute;left:12px;top:9px}
.main-nav{left:0;top:121px;width:1200px;height:51px;background:var(--nav);border-top:1px solid #4b4b4b}
.main-nav ul{list-style:none;display:flex;gap:29px;position:absolute;left:74px;top:17px;color:#eee;font-size:14px}
.socials{right:75px;top:10px;display:flex;gap:8px}
.socials i{display:block;width:31px;height:31px;border:2px solid #ddd;border-radius:50%}

/* hero */
.hero-photo{left:0;top:172px;width:1200px;height:557px;background:linear-gradient(120deg,#6d5a4c 0%,#a79b8d 35%,#5a6673 60%,#8a7c6e 100%)}
.hero-panel{left:795px;top:172px;width:330px;height:463px}
.hero-panel svg{position:absolute;left:0;top:0}
.hero-copy{position:absolute;left:27px;top:28px;width:280px;color:var(--white)}
.date-tag{display:inline-block;background:var(--orange);color:var(--white);font-size:13px;padding:4px 8px;font-weight:600}
.hero-title{font-size:24px;font-weight:600;line-height:27px;margin-top:10px}
.hero-text{font-size:13px;line-height:20px;margin-top:14px}
.btn{display:inline-block;border:2px solid var(--white);color:var(--white);font-size:13px;font-weight:600;text-align:center}
.hero-btns{position:absolute;left:45px;top:298px;display:flex;gap:9px}
.hero-btns .btn{width:116px;height:40px;line-height:36px}
.slider-track{left:222px;top:729px;width:299px;height:7px;background:var(--orange)}

/* event tiles */
.tile{top:736px;width:300px;height:300px}
.tile .photo{position:absolute;inset:0}
.tile .info{position:absolute;left:26px;top:156px;color:var(--white)}
.tile .date{background:var(--teal);font-size:12px;padding:3px 6px;font-weight:600;display:inline-block}
.tile h3{font-size:17px;font-weight:600;line-height:22px;margin-top:8px}
.tile .btns{display:flex;gap:9px;margin-top:8px}
.tile .btn{width:89px;height:30px;line-height:26px;font-size:12px}
.tile .btn.book{border-color:var(--orange);color:var(--orange)}

/* news */
.news{left:0;top:1036px;width:1200px;height:463px;background:var(--paper)}
.section-title{width:1200px;text-align:center;color:var(--charcoal);font-size:23px;font-weight:600;letter-spacing:.5px}
.section-sub{width:1200px;text-align:center;color:var(--muted);font-size:13px}
.news-card{top:1175px;width:332px;height:270px;background:var(--white)}
.news-card .head{height:92px;background:var(--orange);color:var(--white);font-size:17px;font-weight:600;line-height:22px;padding:23px 28px 0}
.news-card .pip{position:absolute;left:32px;top:91px;width:0;height:0;border-left:6px solid transparent;border-right:6px solid transparent;border-top:7px solid var(--orange)}
.news-card p{font-size:13px;line-height:22px;color:var(--muted);padding:20px 28px 0}
.news-card .more{position:absolute;right:8px;bottom:0;width:100%;height:22px;background:#fdf2ea;color:var(--orange);font-size:11px;text-align:right;padding:4px 8px 0 0}

/* features */
.feature{top:1556px;width:332px;height:355px}
.feature .photo{position:absolute;left:0;top:0;width:332px;height:238px}
.feature .band{position:absolute;left:0;top:238px;width:332px;height:117px;color:var(--white);text-align:center}
.feature h3{font-size:18px;font-weight:600;padding-top:20px}
.feature .btn{width:88px;height:30px;line-height:26px;font-size:13px;margin-top:14px}
.feature .badge{position:absolute;left:130px;top:168px;width:72px;height:72px}
.blue{background:var(--blue)} .green{background:var(--teal)} .orange{background:var(--orange)}

/* sports */
.sports{left:0;top:1966px;width:1200px;height:463px;background:linear-gradient(100deg,#6d5b4f 0%,#b59a84 40%,#5e8fb0 70%,#cfa58a 100%)}
.sports h2{position:absolute;left:0;top:188px;width:1200px;text-align:center;color:var(--white);font-size:44px;font-weight:600}
.sports p{position:absolute;left:0;top:246px;width:1200px;text-align:center;color:var(--white);font-size:13px}

/* footer */
.site-footer{left:0;top:2429px;width:1200px;height:238px;background:var(--charcoal);color:#ddd}
.foot-col{top:44px;font-size:13.5px;line-height:22.5px}
.foot-brand{left:915px;top:80px;color:var(--white);font-weight:700;font-size:30px;line-height:32px;letter-spacing:1px}
.copyright{left:0;top:188px;width:1200px;text-align:center;font-size:13px;color:#ccc}
</style>
</head>
<body>

<header class="site-header abs">
  <div class="brand abs">BRACKMOOR<br>HALLS</div>
  <div class="brand-divider abs"></div>
  <div class="tagline abs">Dorvale's Premier Entertainment &amp; Sporting Center</div>
  <div class="util-links abs">Gift Voucher<span>|</span>Join Our Mailing List<span>|</span>My Account<span>|</span>Basket<span>|</span>Register</div>
  <div class="box-office abs">Box Office : <b>01632 960 482</b></div>
  <div class="search abs"><svg width="13" height="13" viewBox="0 0 13 13"><circle cx="5.5" cy="5.5" r="4.3" fill="none" stroke="#777" stroke-width="1.6"/><line x1="8.6" y1="8.6" x2="12" y2="12" stroke="#777" stroke-width="1.6"/></svg>Search</div>
</header>

<nav class="main-nav abs">
  <ul><li>What's On</li><li>Conferencing &amp; Events</li><li>Sports &amp; Leisure</li><li>Lantern Theatre</li><li>Plan Your Visit</li><li>News</li><li>Discover More</li><li>Contact</li></ul>
  <div class="socials abs"><i></i><i></i><i></i></div>
</nav>

<div class="hero-photo abs" role="img" aria-label="Guests mingling and talking at a networking reception"></div>
<div class="hero-panel abs">
  <svg width="330" height="463" viewBox="0 0 330 463"><polygon points="0,0 330,0 330,463 0,380" fill="#0f7e6a" fill-opacity=".95"/></svg>
  <div class="hero-copy">
    <span class="date-tag">MONDAY 7 JAN 2017</span>
    <div class="hero-title">THE STANDARD<br>LOREM IPSUM PASSAGE</div>
    <p class="hero-text">Lorem ipsum dolor sit amet, consectetur adipiscing elit, sed do eiusmod tempor incididunt ut labore et dolore magna aliqua. Ut enim ad minim veniam, quis nostrud exercitation ullamco laboris nisi ut aliquip ex ea commodo consequat.</p>
  </div>
  <div class="hero-btns"><span class="btn">MORE</span><span class="btn">BOOK</span></div>
</div>
<div class="slider-track abs"></div>

<div class="tile abs" style="left:0">
  <div class="photo" role="img" aria-label="Large crowd at an outdoor concert" style="background:linear-gradient(160deg,#6d6fa8,#3b3560)"></div>
  <div class="info"><span class="date">MONDAY 7 JAN 2017</span><h3>The standard<br>Lorem Ipsum passage</h3><div class="btns"><span class="btn">MORE</span><span class="btn book">BOOK</span></div></div>
</div>
<div class="tile abs" style="left:300px">
  <div class="photo" role="img" aria-label="Visitors at an exhibition hall trade show" style="background:linear-gradient(160deg,#9aa4ad,#40464d)"></div>
  <div class="info"><span class="date">MONDAY 7 JAN 2017</span><h3>The standard<br>Lorem Ipsum passage</h3><div class="btns"><span class="btn">MORE</span><span class="btn book">BOOK</span></div></div>
</div>
<div class="tile abs" style="left:600px">
  <div class="photo" role="img" aria-label="Evening exhibition space with warm lighting" style="background:linear-gradient(160deg,#8a6a2c,#2f2a1f)"></div>
  <div class="info"><span class="date">MONDAY 7 JAN 2017</span><h3>The standard<br>Lorem Ipsum passage</h3><div class="btns"><span class="btn">MORE</span><span class="btn book">BOOK</span></div></div>
</div>
<div class="tile abs" style="left:900px">
  <div class="photo" role="img" aria-label="Crowd exercising at an outdoor festival" style="background:linear-gradient(180deg,#b9cfe0 0%,#7b8a6a 45%,#6a4f55 100%)"></div>
  <div class="info"><span class="date">MONDAY 7 JAN 2017</span><h3>The standard<br>Lorem Ipsum passage</h3><div class="btns"><span class="btn">MORE</span><span class="btn book">BOOK</span></div></div>
</div>

<section class="news abs">
  <h2 class="section-title abs" style="top:50px">LATEST FROM BRACKMOOR</h2>
  <div class="section-sub abs" style="top:84px">See All News</div>
</section>
<article class="news-card abs" style="left:73px"><div class="head">The standard Lorem Ipsum passage used since.</div><span class="pip"></span><p>Ut enim ad minim veniam, quis nostrud Duis aute irure dolor in reprehenderit in cillum dolore eu fugiat nulla pariatur. Ut aute irure dolor in reprehenderit in cillum dolore eu fugiat nulla pariatur.</p><div class="more">MORE ▸</div></article>
<article class="news-card abs" style="left:434px"><div class="head">The standard Lorem Ipsum passage used since.</div><span class="pip"></span><p>Ut enim ad minim veniam, quis nostrud Duis aute irure dolor in reprehenderit in cillum dolore eu fugiat nulla pariatur. Ut aute irure dolor in reprehenderit in cillum dolore eu fugiat nulla pariatur.</p><div class="more">MORE ▸</div></article>
<article class="news-card abs" style="left:793px"><div class="head">The standard Lorem Ipsum passage used since.</div><span class="pip"></span><p>Ut enim ad minim veniam, quis nostrud Duis aute irure dolor in reprehenderit in cillum dolore eu fugiat nulla pariatur. Ut aute irure dolor in reprehenderit in cillum dolore eu fugiat nulla pariatur.</p><div class="more">MORE ▸</div></article>

<div class="feature abs" style="left:73px">
  <div class="photo" role="img" aria-label="Speaker presenting to a conference audience" style="background:linear-gradient(150deg,#b06a3a,#3d2a22)"></div>
  <div class="band blue"><h3>CONFERENCES &amp; EVENTS</h3><span class="btn">MORE</span></div>
  <svg class="badge" viewBox="0 0 72 72"><polygon points="36,0 72,18 72,72 0,72 0,18" fill="#035bde"/><circle cx="36" cy="34" r="7" fill="none" stroke="#fff" stroke-width="2"/><path d="M22 54 q14-14 28 0" fill="none" stroke="#fff" stroke-width="2"/></svg>
</div>
<div class="feature abs" style="left:434px">
  <div class="photo" role="img" aria-label="Friends celebrating at an evening party" style="background:linear-gradient(150deg,#4a3b3a,#a37a5f)"></div>
  <div class="band green"><h3>PARTIES AT BRACKMOOR</h3><span class="btn">MORE</span></div>
  <svg class="badge" viewBox="0 0 72 72"><polygon points="36,0 72,18 72,72 0,72 0,18" fill="#0f7e6a"/><path d="M26 26 l4 16 M46 26 l-4 16 M30 42 v10 M42 42 v10 M25 52 h10 M37 52 h10" stroke="#fff" stroke-width="2" fill="none"/></svg>
</div>
<div class="feature abs" style="left:793px">
  <div class="photo" role="img" aria-label="Hands typing on a laptop keyboard" style="background:linear-gradient(150deg,#c9c9c9,#6c6c6c)"></div>
  <div class="band orange"><h3>CO-WORKING HUB</h3><span class="btn">MORE</span></div>
  <svg class="badge" viewBox="0 0 72 72"><polygon points="36,0 72,18 72,72 0,72 0,18" fill="#d57835"/><rect x="22" y="24" width="22" height="16" rx="2" fill="none" stroke="#fff" stroke-width="2"/><rect x="30" y="32" width="22" height="16" rx="2" fill="#d57835" stroke="#fff" stroke-width="2"/></svg>
</div>

<section class="sports abs" role="img" aria-label="People running on treadmills in a gym">
  <h2>SPORTS &amp; LEISURE</h2>
  <p>CLICK FOR MORE INFORMATION</p>
</section>

<footer class="site-footer abs">
  <div class="foot-col abs" style="left:73px">Brackmoor Entertainment Venue<br>Harrow Lane<br>Chalbury<br>Dorvale<br>DV4 7QX</div>
  <div class="foot-col abs" style="left:345px">What's On<br>Conferencing &amp; Events<br>Sports &amp; Leisure<br>Lantern Theatre</div>
  <div class="foot-col abs" style="left:613px">Plan Your Visit<br>News<br>Discover More<br>Contact Us</div>
  <div class="foot-brand abs">BRACKMOOR<br>HALLS</div>
  <div class="copyright abs">Copyright © 2016 Brackmoorhalls.co.uk All Rights Reserved</div>
</footer>

</body>
</html>
```